Yacht, Boats, Watersports company needs a redesign of business card

Hello Designers!
We are a Boat dealership company that sells fun in the water, we sell boats, Yachts, Kayaks and also yacht WaterSport toys. We are looking to redesign our business cards in to something a little bit more sophisticated. in a way that we can make better use of our company colors. I'm attaching a zipped file containing the company 3 sets of company logo which one is an horizontal another one is a vertical and also a chromed 3d logo. Also is included two set of business cards that we use and also some designs that i think it's interesting. We use PMS 2026c Orange and PMS 7687C Blue. I would like to see at least two different options with the orange as accent and also using blue as an accent color. It's really important for the business cards to have a font option and size that is legible to most people. Our current website is wwww.coralpennant.com. Please visit if you want to have a better feeling of the Boat dealership
You can send Single sided or double side options. We are now using single sided but we may be open for a double side option if we really like the design.
Target Market(s)
Marine, boat sales, yacht sales, water toys sales/
Contact Information for Business Card
Name: Dale Whitcombe
Address: 212 North Fenwick Lane,
Harbor Point, FL 33910
Phone: 954-731-8842
Fax: 954:731-8843
Cell: 954-382-1490
Email: dw@coralpennant.com
Website: coralpennant.com
Requirements
Must have
- the current information of the business card provided.
logo
use the PMS Colors
Nice to have
- a touch of elegance and sophistication but simple
Should not have
- should not have any typography that is hard to read, the card should be simple but yet sophisticated.

```html
<!DOCTYPE html>
<html lang="en">
<head>
<meta charset="utf-8">
<title>Coral Pennant – Business Card</title>
<link rel="stylesheet" href="https://fonts.googleapis.com/css2?family=Poppins:wght@400;600&family=Roboto+Condensed:wght@500&display=swap">
<style>
  :root {
    --pms-orange: #ee8823;
    --pms-blue: #1f6db3;
    --text-grey: #4a4a4a;
    --card-white: #ffffff;
    --backdrop: #1d1d1d;
    --gold: #ffd53d;
  }
  * { margin: 0; padding: 0; box-sizing: border-box; }
  html, body { width: 1125px; height: 1200px; overflow: hidden; background: var(--backdrop); }
  .sheet { position: relative; width: 1125px; height: 1200px; }
  .card { position: absolute; left: 162px; width: 800px; height: 457px; overflow: hidden; }
  .card--front { top: 113px; background: var(--card-white); }
  .card--back { top: 629px; background: var(--pms-orange); }
  .front-sweep { position: absolute; inset: 0; }

  .brand { position: absolute; left: 54px; top: 120px; display: flex; align-items: center; gap: 14px; }
  .brand__dot { width: 40px; height: 40px; border-radius: 50%; background: var(--pms-orange); }
  .brand__name { font-family: "Poppins", sans-serif; font-weight: 600; font-size: 30px; letter-spacing: 1px; color: var(--pms-blue); white-space: nowrap; }

  .address { position: absolute; left: 54px; top: 243px; font-family: "Poppins", sans-serif; font-size: 18px; line-height: 23px; color: var(--text-grey); }
  .contacts { position: absolute; left: 54px; top: 301px; list-style: none; font-family: "Poppins", sans-serif; font-size: 18px; line-height: 22.7px; color: var(--text-grey); }
  .contacts li { display: flex; align-items: center; gap: 11px; }
  .contacts svg { width: 16px; height: 16px; fill: var(--pms-blue); flex: none; }

  .holder { position: absolute; right: 64px; top: 372px; font-family: "Roboto Condensed", sans-serif; font-weight: 500; font-size: 42px; color: var(--pms-blue); letter-spacing: 0.5px; white-space: nowrap; }

  .back-brand { position: absolute; inset: 0; display: flex; flex-direction: column; align-items: center; justify-content: center; gap: 34px; padding-top: 20px; }
  .back-brand__dot { width: 110px; height: 110px; border-radius: 50%; background: var(--gold); }
  .back-brand__name { font-family: "Poppins", sans-serif; font-weight: 600; font-size: 40px; letter-spacing: 1px; color: var(--gold); white-space: nowrap; }
</style>
</head>
<body>
<main class="sheet">
  <section class="card card--front">
    <svg class="front-sweep" viewBox="0 0 800 457" aria-hidden="true">
      <path d="M435 0 C610 70 760 190 800 350 L800 0 Z" fill="var(--pms-blue)"/>
      <path d="M435 0 C620 70 770 220 790 420" fill="none" stroke="var(--pms-orange)" stroke-width="6"/>
    </svg>

    <div class="brand">
      <span class="brand__dot"></span>
      <span class="brand__name">CORAL PENNANT</span>
    </div>

    <p class="address">212 North Fenwick Lane<br>Harbor Point, FL 33910</p>

    <ul class="contacts">
      <li><svg viewBox="0 0 16 16"><path d="M3 1l3 3-1.5 2c1 2 3 4 5 5L11.5 9.5l3 3-1.5 2.5C7 15 1 9 .5 3z"/></svg>954-731-8842</li>
      <li><svg viewBox="0 0 16 16"><path d="M4 0h8a1 1 0 011 1v14a1 1 0 01-1 1H4a1 1 0 01-1-1V1a1 1 0 011-1zm1 2v10h6V2z"/></svg>954-382-1490</li>
      <li><svg viewBox="0 0 16 16"><path d="M4 1h8v4H4zM1 6h14v6h-2v3H3v-3H1zm4 5v3h6v-3z"/></svg>954-731-8843</li>
      <li><svg viewBox="0 0 16 16"><path d="M1 4h14v9H1zm1 1l6 4 6-4z"/></svg>dw@coralpennant.com</li>
      <li><svg viewBox="0 0 16 16"><circle cx="8" cy="8" r="7"/></svg>coralpennant.com</li>
    </ul>

    <p class="holder">DALE WHITCOMBE</p>
  </section>

  <section class="card card--back">
    <div class="back-brand">
      <span class="back-brand__dot"></span>
      <span class="back-brand__name">CORAL PENNANT</span>
    </div>
  </section>
</main>
</body>
</html>
```